Treatment Info-Graphic Poster

22 x 28 poster. We need a design for a poster to hang in our treatment rooms that quickly compares different treatments we offer and sets expectations for the patient. Attached is something I very quickly created on Excel, but we would like one that matches our company colors and looks much more polished. I have attached a info-graphic we have had designed prior for reference.

Target Market(s)

Osteoarthritis of the knee patients treatment comparison info graphic for poster

Font styles to use
Serif

Colors
85cae6
f78f20

Requirements
Must have
• Branded treatment comparison table
Nice to have
• Treatment graphics

```html
<!DOCTYPE html>
<html lang="en">
<head>
<meta charset="utf-8">
<title>Knee OA Treatment Comparison</title>
<link href="https://fonts.googleapis.com/css2?family=Montserrat:wght@400;600;700;800&family=Lora:wght@400;500&display=swap" rel="stylesheet">
<style>
:root{
  --teal:#5ea9bb;
  --teal-dark:#3f95a8;
  --orange:#f7901f;
  --orange-dark:#ee8416;
  --panel:#5f6063;
  --panel-line:#88898c;
  --bg-top:#5c5d60;
  --bg-bottom:#c9cacc;
  --cell-top:#ffffff;
  --cell-bottom:#ececed;
  --white:#ffffff;
}
*{box-sizing:border-box;margin:0;padding:0}
html,body{width:1200px;height:963px;overflow:hidden;background:#fff}
body{font-family:"Montserrat",Arial,sans-serif;position:relative}
.poster{position:absolute;left:86px;top:78px;width:1028px;height:808px;
  background:linear-gradient(180deg,var(--bg-top) 0%,#8a8b8d 35%,var(--bg-bottom) 100%);
  box-shadow:0 14px 22px rgba(0,0,0,.25);overflow:hidden}
.footer-band{position:absolute;left:0;right:0;top:706px;bottom:0;z-index:0;
  background:linear-gradient(180deg,#66b0c0,var(--teal-dark))}
.title{position:absolute;left:0;right:0;top:32px;text-align:center;color:var(--white);
  font-weight:800;font-size:41px;letter-spacing:.4px;z-index:1}
.disclaimer{position:absolute;left:0;right:0;top:747px;text-align:center;color:var(--white);
  font-size:12.6px;font-weight:600;line-height:19px;z-index:1}

.label-col{position:absolute;left:36px;top:117px;width:242px;height:602px;z-index:2;
  background:var(--panel);border:2px solid #fff;border-radius:14px;overflow:hidden}
.brand{height:117px;background:linear-gradient(180deg,#6fb4c4,var(--teal-dark));
  display:flex;flex-direction:column;align-items:center;justify-content:center;
  color:var(--white);font-family:"Lora",Georgia,serif;font-weight:500}
.brand-name{font-size:31px;line-height:34px}
.brand-sub{font-size:12px;margin-top:4px;letter-spacing:.3px}
.label{height:44px;border-top:2px solid var(--panel-line);display:flex;align-items:center;
  padding-left:21px;color:var(--white);font-size:11.8px;font-weight:700;line-height:16px}
.avg-group{display:flex;border-top:2px solid var(--panel-line)}
.avg-tag{width:46px;background:linear-gradient(180deg,#6fb4c4,var(--teal-dark));display:flex;align-items:center;justify-content:center}
.avg-tag span{transform:rotate(-90deg);white-space:nowrap;color:var(--white);font-weight:700;font-size:11.8px}
.avg-rows{flex:1}
.avg-rows .label{padding-left:12px}
.avg-rows .label:first-child{border-top:none}

.col{position:absolute;top:117px;width:174px;height:602px;z-index:2;border:2px solid #fff;border-radius:14px;overflow:hidden;background:var(--cell-bottom)}
.col.c1{left:285px}.col.c2{left:463px}.col.c3{left:642px}.col.c4{left:821px}
.head{height:117px;padding:9px 10px 0 13px;color:var(--white);position:relative}
.teal .head{background:linear-gradient(180deg,#6fb4c4,var(--teal-dark))}
.orange .head{background:linear-gradient(180deg,#f89a2c,var(--orange-dark))}
.head h2{font-size:14.6px;font-weight:700;line-height:23px;white-space:nowrap}
.head svg.icon{position:absolute;right:10px;top:30px}
.grades{position:absolute;left:13px;right:12px;top:69px;font-size:5.6px;line-height:8px;font-weight:400}
.grades .hd{text-align:right;white-space:nowrap}
.grades .row{display:flex;justify-content:space-between;white-space:nowrap}
.grades .row span:last-child{width:20px}
.cell{height:44px;border-top:1px solid #d4d5d7;background:linear-gradient(180deg,var(--cell-top),var(--cell-bottom));
  display:flex;align-items:center;justify-content:center}
.tick{width:38px;height:27px;fill:none;stroke-width:4.5;stroke-linecap:square}
.teal .tick{stroke:var(--teal)}
.orange .tick{stroke:var(--orange)}
</style>
</head>
<body>
<main class="poster">
  <div class="footer-band"></div>
  <h1 class="title">KNEE OA TREATMENT COMPARISON</h1>

  <section class="label-col">
    <div class="brand"><span class="brand-name">Arcline</span><span class="brand-sub">Knee Specialists</span></div>
    <div class="label">Cushion &amp; Lubricate</div>
    <div class="label">Decrease Inflammation</div>
    <div class="label">Stimulates Synovial<br>Production of HA</div>
    <div class="label">Healing Properties</div>
    <div class="label">Reparative Properties</div>
    <div class="label">Potential Cartilage<br>Regeneration</div>
    <div class="avg-group">
      <div class="avg-tag"><span>On Average,</span></div>
      <div class="avg-rows">
        <div class="label">Benefits Last 4-6 Months</div>
        <div class="label">Benefits Last 6-12 Months</div>
        <div class="label">Benefits Last 18+ Months</div>
      </div>
    </div>
    <div class="label">Corrects Biomechanics<br>&amp; Stabilizes Joint</div>
    <div class="label">Covered by MOST Insurance</div>
  </section>

  <svg width="0" height="0" style="position:absolute"><defs><symbol id="tk" viewBox="0 0 38 27"><path d="M3 13 L14 23 L35 3"/></symbol></defs></svg>

  <section class="col c1 teal">
    <div class="head"><h2>Hyaluronic Acid<br>(HA)</h2>
      <svg class="icon" width="26" height="26" viewBox="0 0 26 26" fill="none" stroke="#fff" stroke-width="2.4"><path d="M3 23 L14 12 M10 8 L18 16 M16 4 L22 10 M19 7 L24 2"/></svg>
      <div class="grades"><div class="hd">OA Grade</div>
        <div class="row"><span>Single Injection (Flexa One)</span><span>1,2,3,4</span></div>
        <div class="row"><span>Single Injection (Lubrion)</span><span>1,2,3,4</span></div>
        <div class="row"><span>3 Part Injection Series (Synovel)</span><span>1,2,3,4</span></div>
        <div class="row"><span>3/4 Part Injection Series (Viscora)</span><span>1,2,3,4</span></div></div>
    </div>
    <div class="cell"><svg class="tick"><use href="#tk"/></svg></div>
    <div class="cell"><svg class="tick"><use href="#tk"/></svg></div>
    <div class="cell"><svg class="tick"><use href="#tk"/></svg></div>
    <div class="cell"></div><div class="cell"></div><div class="cell"></div>
    <div class="cell"><svg class="tick"><use href="#tk"/></svg></div>
    <div class="cell"></div><div class="cell"></div><div class="cell"></div>
    <div class="cell"><svg class="tick"><use href="#tk"/></svg></div>
  </section>

  <section class="col c2 orange">
    <div class="head"><h2>Platelet Rich<br>Plasma (PRP)</h2>
      <svg class="icon" width="26" height="26" viewBox="0 0 26 26" fill="none" stroke="#fff" stroke-width="2.4"><path d="M3 23 L14 12 M10 8 L18 16 M16 4 L22 10 M19 7 L24 2"/></svg>
      <div class="grades"><div class="hd">OA Grade</div>
        <div class="row"><span>Single Injection (Platova)</span><span>1,2</span></div>
        <div class="row"><span>2 Part Injection Series</span><span>3, 4</span></div></div>
    </div>
    <div class="cell"><svg class="tick"><use href="#tk"/></svg></div>
    <div class="cell"><svg class="tick"><use href="#tk"/></svg></div>
    <div class="cell"><svg class="tick"><use href="#tk"/></svg></div>
    <div class="cell"><svg class="tick"><use href="#tk"/></svg></div>
    <div class="cell"></div><div class="cell"></div>
    <div class="cell"><svg class="tick"><use href="#tk"/></svg></div>
    <div class="cell"><svg class="tick"><use href="#tk"/></svg></div>
    <div class="cell"></div><div class="cell"></div><div class="cell"></div>
  </section>

  <section class="col c3 teal">
    <div class="head"><h2>Stem Cell Therapy<br>&amp; PRP</h2>
      <svg class="icon" width="26" height="26" viewBox="0 0 26 26" fill="none" stroke="#fff" stroke-width="2.4"><path d="M3 23 L14 12 M10 8 L18 16 M16 4 L22 10 M19 7 L24 2"/></svg>
      <div class="grades"><div class="hd">OA Grade</div>
        <div class="row"><span>Single Injection</span><span>1,2,3,4</span></div></div>
    </div>
    <div class="cell"><svg class="tick"><use href="#tk"/></svg></div>
    <div class="cell"><svg class="tick"><use href="#tk"/></svg></div>
    <div class="cell"><svg class="tick"><use href="#tk"/></svg></div>
    <div class="cell"><svg class="tick"><use href="#tk"/></svg></div>
    <div class="cell"><svg class="tick"><use href="#tk"/></svg></div>
    <div class="cell"><svg class="tick"><use href="#tk"/></svg></div>
    <div class="cell"><svg class="tick"><use href="#tk"/></svg></div>
    <div class="cell"><svg class="tick"><use href="#tk"/></svg></div>
    <div class="cell"><svg class="tick"><use href="#tk"/></svg></div>
    <div class="cell"></div><div class="cell"></div>
  </section>

  <section class="col c4 orange">
    <div class="head"><h2>Knee Brace<br>(s)</h2>
      <svg class="icon" width="26" height="26" viewBox="0 0 26 26" fill="#fff"><circle cx="18" cy="4" r="3"/><path d="M11 8 L18 9 L15 15 L19 19 L17 24 L13 18 L9 22 L5 21 L11 15 L12 11 L8 13 Z"/></svg>
      <div class="grades"><div class="hd">OA Grade</div>
        <div class="row"><span>Kinetra 2</span><span>1,2,3,4</span></div>
        <div class="row"><span>Patellar Stabilization</span><span>1,2,3,4</span></div></div>
    </div>
    <div class="cell"></div><div class="cell"></div><div class="cell"></div>
    <div class="cell"></div><div class="cell"></div><div class="cell"></div>
    <div class="cell"><svg class="tick"><use href="#tk"/></svg></div>
    <div class="cell"><svg class="tick"><use href="#tk"/></svg></div>
    <div class="cell"><svg class="tick"><use href="#tk"/></svg></div>
    <div class="cell"><svg class="tick"><use href="#tk"/></svg></div>
    <div class="cell"><svg class="tick"><use href="#tk"/></svg></div>
  </section>

  <p class="disclaimer">Treatment outcomes vary by individual. Treatment benefits and length of efficacy are not guaranteed. In some cases, patient’s<br>do not respond to treatment. Multiple treatments may be recommended or necessary for the best outcomes.</p>
</main>
</body>
</html>
```